Our companies name is The Gilded Ladle and we specialize in craft cupcakes, what I mean by that is that we bake our cupcakes with craft beer and other alcoholic drinks. We are trying to focus on being elegant but at the same time unpretentious. Since we are incorporating beer in our cupcakes we want the business card to have our logo in the front and our information in the back.

Once we select the best design we will provide the contact information to be added. Thank you.

Industry/Entity Type

Business

Font styles to use
Decorative
Script

Requirements
Must have
• Round corners
Should not have
• Square corners

```html
<!DOCTYPE html>
<html lang="en">
<head>
<meta charset="utf-8">
<title>The Gilded Ladle — Business Card</title>
<link href="https://fonts.googleapis.com/css2?family=Michroma&display=swap" rel="stylesheet">
<style>
  :root {
    --backdrop: #8e8f8f;
    --card: #ffffff;
    --ink: #1b1b1b;
    --ink-soft: #555555;
    --accent: #f05a22;
    --accent-deep: #d9461a;
    --badge: #1c1c1c;
    --badge-ring: #d8262e;
    --rule: #9a9a9a;
  }
  * { box-sizing: border-box; margin: 0; padding: 0; }
  html, body { width: 1200px; height: 771px; overflow: hidden; }
  body {
    background: var(--backdrop);
    font-family: "Michroma", sans-serif;
    display: flex;
    align-items: center;
    justify-content: center;
    gap: 40px;
  }
  .card {
    position: relative;
    width: 540px;
    height: 309px;
    background: var(--card);
    border-radius: 18px;
    overflow: hidden;
    box-shadow: 0 10px 24px rgba(0,0,0,0.25);
  }
  .brand-mark {
    display: flex;
    align-items: center;
    gap: 10px;
    color: var(--ink);
    letter-spacing: 0.04em;
  }
  .brand-mark .dot {
    flex: none;
    border-radius: 50%;
    background: var(--badge-ring);
  }
  .card-front .brand-mark {
    position: absolute;
    left: 50%;
    top: 50%;
    transform: translate(-50%, -50%);
    font-size: 20px;
    white-space: nowrap;
  }
  .card-front .brand-mark .dot { width: 22px; height: 22px; }

  .swoosh { position: absolute; inset: 0; width: 100%; height: 100%; }

  .card-back .brand-mark {
    position: absolute;
    left: 222px;
    top: 42px;
    font-size: 14px;
    white-space: nowrap;
  }
  .card-back .brand-mark .dot { width: 16px; height: 16px; }

  .identity {
    position: absolute;
    right: 300px;
    top: 128px;
    text-align: right;
    font-size: 8.5px;
    line-height: 1.8;
    color: var(--ink-soft);
    letter-spacing: 0.06em;
  }
  .identity .person {
    color: var(--accent);
    font-size: 11px;
    letter-spacing: 0.1em;
  }
  .identity .role { margin-bottom: 10px; }
  .divider {
    position: absolute;
    left: 258px;
    top: 124px;
    width: 1px;
    height: 92px;
    background: var(--rule);
  }
  .contacts {
    position: absolute;
    left: 270px;
    top: 126px;
    list-style: none;
    font-size: 9.5px;
    color: var(--ink-soft);
    letter-spacing: 0.08em;
  }
  .contacts li {
    display: flex;
    align-items: center;
    gap: 8px;
    height: 17px;
  }
  .contacts .icon { width: 12px; height: 12px; flex: none; }
</style>
</head>
<body>

  <section class="card card-front" aria-label="Card front">
    <div class="brand-mark"><span class="dot"></span>The Gilded Ladle</div>
  </section>

  <section class="card card-back" aria-label="Card back">
    <svg class="swoosh" viewBox="0 0 540 309" preserveAspectRatio="none" aria-hidden="true">
      <path d="M0 60 C40 150 150 250 430 309 L0 309 Z" fill="var(--accent)"/>
      <path d="M0 40 C30 140 130 240 360 309 L0 309 Z" fill="var(--badge)"/>
      <path d="M0 58 C35 155 150 255 380 309 L0 309 Z" fill="var(--card)"/>
      <path d="M0 92 C50 190 170 270 430 309 L0 309 Z" fill="var(--accent)"/>
      <path d="M0 110 C60 205 190 280 400 309 L0 309 Z" fill="var(--card)"/>
    </svg>

    <div class="brand-mark"><span class="dot"></span>The Gilded Ladle</div>

    <div class="identity">
      <div class="person">CLARA HOLLIS</div>
      <div class="role">Owner / C.E.O</div>
      <div>Suite # 118, Oak Bldg,</div>
      <div>NY 40217</div>
    </div>

    <div class="divider"></div>

    <ul class="contacts">
      <li>
        <svg class="icon" viewBox="0 0 12 12" aria-hidden="true"><circle cx="6" cy="6" r="6" fill="var(--accent)"/><path d="M4 3 L5 3 L5.6 4.6 L4.9 5.2 C5.3 6.1 5.9 6.7 6.8 7.1 L7.4 6.4 L9 7 L9 8 C9 8.5 8.5 9 8 9 C5.5 9 3 6.5 3 4 C3 3.5 3.5 3 4 3 Z" fill="#fff"/></svg>
        555-214-3390
      </li>
      <li>
        <svg class="icon" viewBox="0 0 12 12" aria-hidden="true"><circle cx="6" cy="6" r="6" fill="var(--accent)"/><rect x="4.2" y="2.6" width="3.6" height="6.8" rx="0.8" fill="#fff"/></svg>
        555-871-4026
      </li>
      <li>
        <svg class="icon" viewBox="0 0 12 12" aria-hidden="true"><circle cx="6" cy="6" r="6" fill="var(--accent)"/><rect x="3" y="5" width="6" height="3.5" rx="0.5" fill="#fff"/><rect x="4" y="3" width="4" height="2" fill="#fff"/></svg>
        555-630-1957
      </li>
      <li>
        <svg class="icon" viewBox="0 0 12 12" aria-hidden="true"><circle cx="6" cy="6" r="6" fill="var(--accent)"/><rect x="3" y="3.8" width="6" height="4.4" fill="#fff"/><path d="M3 3.8 L6 6.3 L9 3.8" fill="none" stroke="var(--accent)" stroke-width="0.7"/></svg>
        clara@gildedladle.com
      </li>
      <li>
        <svg class="icon" viewBox="0 0 12 12" aria-hidden="true"><circle cx="6" cy="6" r="6" fill="var(--accent)"/><circle cx="6" cy="6" r="3" fill="none" stroke="#fff" stroke-width="0.8"/><path d="M3 6 H9 M6 3 C4.8 4.5 4.8 7.5 6 9 M6 3 C7.2 4.5 7.2 7.5 6 9" fill="none" stroke="#fff" stroke-width="0.6"/></svg>
        www.gildedladle.com
      </li>
    </ul>
  </section>

</body>
</html>
```